Four in One (Flexible infographic for Content Management Industry)

See attachment.
A graphic depicting 4 products, where each can stand on its own and each can be combined with others, but where, if all are taken together, the best result is achieved (the "super product").
Intended use is web. See attached file as an example.
The most basic idea is as the attached diagram shows, where 4 rectangles are arranged in a quadrangle, with a middle rectangle in the center representing the combined 4 products. This concept is fine except it is a bit too obvious as it stands. We are looking for either a variation of this or another concept.
The audience is technical + professional + enterprise - NOT consumers. Hence the design should be conservative in nature.
We are aware of tools like as Canva or Pictogram where such graphics are available, but we are looking for something with a bit more imagination and flexibility.
This graphic should be targeted to web sites and be delivered with vector-based (SVG) graphics.

```html
<!DOCTYPE html>
<html lang="en">
<head>
<meta charset="utf-8">
<title>Super Product – Four in One</title>
<link href="https://fonts.googleapis.com/css2?family=Montserrat:wght@600;700;800&display=swap" rel="stylesheet">
<style>
  :root {
    --frame: #e6e7e8;
    --paper: #ffffff;
    --hub: #d1d3d4;
    --ink: #3a3a3c;
    --doc: #52a8b1;
    --security: #3b717f;
    --erp: #52658b;
    --digital: #3d4f62;
    --on-colour: #ffffff;
  }
  * { margin: 0; padding: 0; box-sizing: border-box; }
  html, body { width: 1155px; height: 1200px; overflow: hidden; background: var(--paper); }
  .canvas {
    position: relative;
    width: 1155px; height: 1200px;
    background: var(--paper);
    border: 13px solid var(--frame);
    font-family: "Montserrat", Arial, sans-serif;
    color: var(--on-colour);
  }
  .artwork { position: absolute; left: -13px; top: -13px; }
  .block { position: absolute; }
  .title { position: absolute; font-weight: 700; white-space: nowrap; letter-spacing: 0.2px; }
  .title--large { font-size: 29px; }
  .title--small { font-size: 23px; }
  .rule { position: absolute; height: 2px; background: var(--on-colour); }
  .summary { position: absolute; font-size: 13.6px; font-weight: 700; line-height: 18.3px; }
  .summary--right { text-align: right; }
  .features { position: absolute; list-style: none; font-size: 13.8px; font-weight: 700; line-height: 18.3px; }
  .features li { position: relative; padding-left: var(--indent, 19px); white-space: nowrap; }
  .features li::before {
    content: "";
    position: absolute; left: 1px; top: 5px;
    width: 9px; height: 5px;
    border-left: 2.4px solid var(--on-colour);
    border-bottom: 2.4px solid var(--on-colour);
    transform: rotate(-45deg);
  }
  .hub-name {
    position: absolute; left: 400px; top: 492px; width: 358px;
    text-align: center; color: var(--ink);
    font-weight: 800; font-size: 62px; line-height: 58px; letter-spacing: -1px;
  }
</style>
</head>
<body>
<div class="canvas">
  <svg class="artwork" width="1155" height="1200" viewBox="0 0 1155 1200" aria-hidden="true">
    <!-- quadrant backings -->
    <path d="M95 230 A144 144 0 0 1 239 86 H560 V557 H95 Z" fill="var(--frame)"/>
    <path d="M594 86 H915 A144 144 0 0 1 1059 230 V557 H594 Z" fill="var(--frame)"/>
    <path d="M95 594 H560 V1064 H239 A144 144 0 0 1 95 920 Z" fill="var(--frame)"/>
    <path d="M594 594 H1059 V920 A144 144 0 0 1 915 1064 H594 Z" fill="var(--frame)"/>
    <!-- quadrant panels -->
    <path d="M113 235 A130 130 0 0 1 243 105 H541 V539 H113 Z" fill="var(--doc)"/>
    <path d="M611 105 H911 A130 130 0 0 1 1041 235 V539 H611 Z" fill="var(--security)"/>
    <path d="M113 611 H543 V1046 H243 A130 130 0 0 1 113 916 Z" fill="var(--erp)"/>
    <path d="M611 611 H1041 V916 A130 130 0 0 1 911 1046 H611 Z" fill="var(--digital)"/>
    <!-- hub -->
    <circle cx="579" cy="575" r="173" fill="var(--paper)"/>
    <circle cx="579" cy="575" r="158" fill="var(--hub)"/>
    <!-- icon badges -->
    <g>
      <circle cx="460" cy="457" r="60" fill="var(--paper)"/>
      <circle cx="460" cy="457" r="40" fill="var(--doc)"/>
      <g fill="none" stroke="var(--on-colour)" stroke-width="1.8" stroke-linejoin="round">
        <path d="M444 433 H469 L476 440 V478 H444 Z"/>
        <path d="M469 433 V440 H476"/>
        <path d="M450 446 H470 M450 452 H470 M450 458 H470 M450 464 H470 M450 470 H464"/>
      </g>
    </g>
    <g>
      <circle cx="697" cy="457" r="60" fill="var(--paper)"/>
      <circle cx="697" cy="457" r="40" fill="var(--security)"/>
      <g fill="none" stroke="var(--on-colour)" stroke-width="3" stroke-linejoin="round" stroke-linecap="round">
        <path d="M697 431 L717 439 V457 C717 470 708 478 697 483 C686 478 677 470 677 457 V439 Z"/>
        <path d="M688 457 L695 464 L707 450"/>
      </g>
    </g>
    <g>
      <circle cx="460" cy="694" r="60" fill="var(--paper)"/>
      <circle cx="460" cy="694" r="40" fill="var(--erp)"/>
      <g fill="none" stroke="var(--on-colour)" stroke-width="1.8" stroke-linejoin="round">
        <path d="M446 675 H468 V708 H446 Z"/>
        <path d="M451 680 H473 V713 H451 Z" fill="var(--erp)"/>
        <path d="M455 687 H469 M455 692 H469 M455 697 H469 M455 702 H469"/>
      </g>
    </g>
    <g>
      <circle cx="697" cy="694" r="60" fill="var(--paper)"/>
      <circle cx="697" cy="694" r="40" fill="var(--digital)"/>
      <g fill="none" stroke="var(--on-colour)" stroke-width="4" stroke-linecap="round">
        <path d="M674 689 A32 32 0 0 1 720 689"/>
        <path d="M682 697 A21 21 0 0 1 712 697"/>
        <path d="M690 704 A10 10 0 0 1 704 704"/>
      </g>
      <circle cx="697" cy="711" r="5" fill="var(--on-colour)"/>
    </g>
  </svg>

  <div class="hub-name">Super<br>Product</div>

  <!-- Document Management -->
  <h2 class="title title--large" style="left:142px; top:152px;">Document Management</h2>
  <div class="rule" style="left:146px; top:199px; width:362px;"></div>
  <p class="summary summary--right" style="left:120px; top:219px; width:400px;">Streamline document organization, access, and collaboration with easier file storage and sharing, leading to more efficient workflows .</p>
  <ul class="features" style="left:139px; top:301px;">
    <li>Centralized Document Control</li>
    <li>Collaborative Workspace Integration</li>
    <li>Automated Compliance Tracking</li>
    <li>Check 4</li>
  </ul>

  <!-- Security and Compliance -->
  <h2 class="title title--large" style="left:615px; top:152px;">Security and Compliance</h2>
  <div class="rule" style="left:618px; top:200px; width:376px;"></div>
  <p class="summary" style="left:615px; top:218px; width:400px;">Benefit from tailored cloud solutions, secure data storage, and expert disaster recovery planning for reliable and scalable IT operations.</p>
  <ul class="features" style="left:628px; top:298px; --indent:42px;">
    <li>Custom Cloud Solutions</li>
    <li>Secure Data Storage</li>
    <li>Expert Disaster Recovery</li>
    <li>Check 4</li>
  </ul>

  <!-- Enterprise Resource Planning -->
  <h2 class="title title--small" style="left:143px; top:756px;">Enterprise Resource Planning</h2>
  <div class="rule" style="left:146px; top:794px; width:352px;"></div>
  <p class="summary summary--right" style="left:110px; top:812px; width:390px;">Simplify management across finance, sales, and operations, enabling better decision-making and improved productivity.</p>
  <ul class="features" style="left:156px; top:902px; --indent:23px;">
    <li>Integrated Business Processes</li>
    <li>Enhanced Decision-Making</li>
    <li>Productivity Improvement</li>
    <li>Check 4</li>
  </ul>

  <!-- Digital Transformation -->
  <h2 class="title title--small" style="left:629px; top:762px;">Digital Transformation</h2>
  <div class="rule" style="left:633px; top:800px; width:351px;"></div>
  <p class="summary" style="left:630px; top:820px; width:380px;">Turn scanned documents into easily searchable digital archives, boosting efficiency and accessibility.</p>
  <ul class="features" style="left:636px; top:908px; --indent:29px;">
    <li>Instant searchable Archives with OCR</li>
    <li>Automated Document Classification</li>
    <li>TeamPortal and Cloud Blob Ready</li>
    <li>Check 4</li>
  </ul>
</div>
</body>
</html>
```